TA BRAMLEY BUSINESS CARD DESIGN PROJECT

We need to utilize our logo that was expertly created on PixelHarbor and now need to match this with a business card design.

```html
<!DOCTYPE html>
<html lang="en">
<head>
<meta charset="UTF-8">
<title>TA BRAMLEY Business Card</title>
<link href="https://fonts.googleapis.com/css2?family=Montserrat:wght@400;700;800&display=swap" rel="stylesheet">
<style>
  :root {
    --brand-blue: #1158ad;
    --ink-black: #1e1e20;
    --paper-white: #ffffff;
    --backdrop: #e6e7ea;
  }
  * { margin: 0; padding: 0; box-sizing: border-box; }
  html, body {
    width: 1200px; height: 900px; overflow: hidden;
    background: var(--backdrop);
    font-family: "Montserrat", Arial, sans-serif;
  }
  .sheet {
    width: 1200px; height: 900px;
    display: flex; flex-direction: column; align-items: center; justify-content: center;
    gap: 36px;
  }
  .card {
    position: relative;
    width: 660px; height: 378px;
    border-radius: 20px;
    overflow: hidden;
    box-shadow: 0 8px 24px rgba(0,0,0,0.18);
  }
  .card-front {
    background: var(--brand-blue);
    display: flex; align-items: center; justify-content: center;
  }
  .wordmark {
    font-weight: 800;
    letter-spacing: 0.12em;
    text-transform: uppercase;
    white-space: nowrap;
  }
  .card-front .wordmark { color: var(--paper-white); font-size: 64px; }
  .card-back { background: var(--paper-white); }
  .card-back .wave { position: absolute; inset: 0; width: 100%; height: 100%; }
  .card-back .wordmark {
    position: absolute; top: 70px; right: 44px;
    color: var(--brand-blue); font-size: 36px;
  }
  .holder {
    position: absolute; top: 148px; left: 0;
    display: flex; align-items: stretch; gap: 20px;
  }
  .holder-bar { width: 22px; background: var(--brand-blue); }
  .holder-name {
    color: var(--brand-blue); font-weight: 800; font-size: 26px; letter-spacing: 0.02em;
  }
  .holder-title {
    color: var(--ink-black); font-weight: 400; font-size: 18px; margin-top: 2px;
  }
  .contacts {
    position: absolute; left: 90px; bottom: 34px;
    list-style: none; color: var(--paper-white); font-size: 17px;
  }
  .contacts li { display: flex; align-items: center; gap: 12px; line-height: 28px; }
  .contacts svg { width: 16px; height: 16px; fill: var(--brand-blue); }
</style>
</head>
<body>
<main class="sheet">
  <section class="card card-front" aria-label="Business card front">
    <span class="wordmark">TA BRAMLEY</span>
  </section>

  <section class="card card-back" aria-label="Business card back">
    <svg class="wave" viewBox="0 0 660 378" preserveAspectRatio="none" aria-hidden="true">
      <path d="M0 282 C190 205 430 232 570 182 C625 162 650 140 660 108 L660 378 L0 378 Z" fill="var(--ink-black)"/>
      <path d="M120 262 C260 218 440 226 570 176 C622 156 645 132 652 104" fill="none" stroke="var(--brand-blue)" stroke-width="4"/>
    </svg>

    <span class="wordmark">TA BRAMLEY</span>

    <div class="holder">
      <span class="holder-bar"></span>
      <div>
        <p class="holder-name">MILES CARTER</p>
        <p class="holder-title">Managing Director</p>
      </div>
    </div>

    <ul class="contacts">
      <li>
        <svg viewBox="0 0 16 16" aria-hidden="true"><path d="M3.5 1 L6 1 L7 4.5 L5.3 5.8 C6.2 7.8 8.2 9.8 10.2 10.7 L11.5 9 L15 10 L15 12.5 C15 13.9 13.9 15 12.5 15 C6.7 15 1 9.3 1 3.5 C1 2.1 2.1 1 3.5 1 Z"/></svg>
        555 010 2030
      </li>
      <li>
        <svg viewBox="0 0 16 16" aria-hidden="true"><path d="M1 3 H15 V13 H1 Z M2 4 L8 9 L14 4 Z" fill-rule="evenodd"/></svg>
        hello@tabramley.com
      </li>
      <li>
        <svg viewBox="0 0 16 16" aria-hidden="true"><circle cx="8" cy="8" r="7"/><path d="M1 8 H15 M8 1 C5 4 5 12 8 15 M8 1 C11 4 11 12 8 15" stroke="#1e1e20" stroke-width="1" fill="none"/></svg>
        www.tabramley.com
      </li>
    </ul>
  </section>
</main>
</body>
</html>
```